Marrowby Water Taxi and Transport Business Card

I need business cards for my new water taxi and freight transport business I have started here in Kodiak Alaska. Kodiak is a remote island in the middle of the gulf of Alaska. There are seven native villages around the island and Kodiak is the #2 fishing port in the United States. We also have the largest Coast Guard Base in the U.S. My company will be providing water taxi and freight transport logistics to the villages and many hunting and fishing lodges as well as remote properties around the island.

I would like a business card that isn't status quo, something that stands out, either in feel or appearance. I do like clean minimal designs but it needs to have the necessary contact info on it.

Target Market(s)

remote lodge / property owners, residents of the many villages around Kodiak and any one wanting to enjoy the great outdoors of Kodiak Alaska

Industry/Entity Type

Business

Contact Information for Business Card

I like clean simple designs that aren't cluttered but still provide the necessary information

Colors
0255a3
3277b5
33a4d5
9bcb3c
add136
fbed22
ffc214
f78f20
f37122

Requirements
Must have
• logo and contact info
• Captain Mason Elwick
• www.marrowbyferryline.com
• mason@marrowbyferryline.com

```html
<!DOCTYPE html>
<html lang="en">
<head>
<meta charset="utf-8">
<title>Marrowby Water Taxi and Transport – Business Card</title>
<link rel="stylesheet" href="https://fonts.googleapis.com/css2?family=Open+Sans:wght@400;600;700&display=swap">
<style>
  :root {
    --page: #e9ecef;
    --white: #ffffff;
    --navy: #0a3f93;
    --blue: #0255a3;
    --mid-blue: #3277b5;
    --sky: #33a4d5;
    --orange: #f7a23a;
    --ink: #1d4f9a;
    --text-light: #eaf3ff;
  }
  * { margin: 0; padding: 0; box-sizing: border-box; }
  html, body { width: 1200px; height: 913px; overflow: hidden; }
  body {
    background: var(--page);
    font-family: "Open Sans", Arial, sans-serif;
    position: relative;
  }
  .card {
    position: absolute;
    top: 306px;
    width: 525px;
    height: 300px;
    border-radius: 18px;
    overflow: hidden;
    box-shadow: 0 10px 28px rgba(0,0,0,.18);
  }
  .card--front { left: 50px; background: var(--white); }
  .card--back { left: 625px; }
  .card__art { position: absolute; inset: 0; width: 100%; height: 100%; }

  .brand {
    position: absolute;
    left: 28px;
    top: 92px;
    display: flex;
    align-items: center;
    gap: 10px;
  }
  .brand__dot {
    width: 22px; height: 22px; border-radius: 50%;
    background: var(--orange);
    flex: none;
  }
  .brand__name {
    font-weight: 700;
    font-size: 17px;
    line-height: 1.15;
    color: var(--blue);
    width: 170px;
  }

  .captain {
    position: absolute;
    right: 26px;
    top: 108px;
    width: 250px;
    text-align: right;
    color: var(--white);
    font-weight: 700;
    font-size: 19px;
    padding-bottom: 6px;
    border-bottom: 1px solid rgba(255,255,255,.7);
  }

  .contact {
    position: absolute;
    left: 26px;
    bottom: 24px;
    list-style: none;
    color: var(--text-light);
    font-size: 13px;
    line-height: 1.55;
  }
  .contact li { display: flex; align-items: center; gap: 8px; }
  .contact svg { width: 11px; height: 11px; flex: none; }

  .back-brand {
    position: absolute;
    left: 0; right: 0;
    top: 98px;
    display: flex;
    flex-direction: column;
    align-items: center;
    gap: 10px;
  }
  .back-brand .brand__dot { width: 30px; height: 30px; }
  .back-brand .brand__name {
    color: var(--white);
    font-size: 20px;
    width: auto;
    text-align: center;
  }
</style>
</head>
<body>

<section class="card card--front" aria-label="Business card front">
  <svg class="card__art" viewBox="0 0 525 300" preserveAspectRatio="none" aria-hidden="true">
    <defs>
      <linearGradient id="frontBlue" x1="0" y1="0" x2="1" y2="1">
        <stop offset="0" stop-color="#2f86cf"/>
        <stop offset="1" stop-color="#0b3f96"/>
      </linearGradient>
    </defs>
    <path d="M300 0 C 250 60, 235 170, 120 215 C 70 235, 30 238, 0 238 L0 300 L525 300 L525 0 Z" fill="var(--sky)"/>
    <path d="M318 0 C 270 70, 250 185, 130 228 C 80 245, 35 248, 0 248 L0 300 L525 300 L525 0 Z" fill="url(#frontBlue)"/>
  </svg>

  <div class="brand">
    <span class="brand__dot"></span>
    <span class="brand__name">Marrowby Water Taxi and Transport</span>
  </div>

  <p class="captain">Captain Mason Elwick</p>

  <ul class="contact">
    <li>
      <svg viewBox="0 0 12 12" aria-hidden="true"><rect x="0.5" y="2" width="11" height="8" rx="1" fill="none" stroke="#f7a23a"/><path d="M1 2.5 L6 7 L11 2.5" fill="none" stroke="#f7a23a"/></svg>
      mason@marrowbyferryline.com
    </li>
    <li>
      <svg viewBox="0 0 12 12" aria-hidden="true"><circle cx="6" cy="6" r="5.2" fill="none" stroke="#f7a23a"/><path d="M1 6 H11 M6 1 C3 4,3 8,6 11 M6 1 C9 4,9 8,6 11" fill="none" stroke="#f7a23a"/></svg>
      www.marrowbyferryline.com
    </li>
  </ul>
</section>

<section class="card card--back" aria-label="Business card back">
  <svg class="card__art" viewBox="0 0 525 300" preserveAspectRatio="none" aria-hidden="true">
    <defs>
      <linearGradient id="backBlue" x1="0" y1="0" x2="1" y2="1">
        <stop offset="0" stop-color="#1f6cc0"/>
        <stop offset="1" stop-color="#0a3a8c"/>
      </linearGradient>
      <linearGradient id="backWave" x1="0" y1="0" x2="1" y2="0">
        <stop offset="0" stop-color="#1e7fd0"/>
        <stop offset="1" stop-color="#39b0e3"/>
      </linearGradient>
    </defs>
    <rect width="525" height="300" fill="url(#backBlue)"/>
    <path d="M180 300 C 230 230, 330 190, 525 140 L525 300 Z" fill="url(#backWave)"/>
    <path d="M180 300 C 230 230, 330 190, 525 140" fill="none" stroke="#ffffff" stroke-width="2.5"/>
  </svg>

  <div class="back-brand">
    <span class="brand__dot"></span>
    <span class="brand__name">Marrowby Water Taxi and Transport</span>
  </div>
</section>

</body>
</html>
```